KVOR Individual and Corporate Development Business Card Design

KVOR needs a business card design that is aligned with it's values and targetted markets. Coherent Lattice of Adaptive Reasoning Method's self diagnosis model and tools, which can be used for personal improvement and team/business performance enhancement, is based on the learnings of over 20 years of medical practitioning. KVOR supercharges personal effectiveness and awareness to also increase team and business performance.

The targetted markets are high performance individuals and teams who aspire seek to enhance their capabilities and achieve their absolute best potential.

Look and feel for the business card design we are looking for is high technology, premium, fresh, new and medical.

Target Market(s)

Industry/Entity Type

Business Consultant

Contact Information for Business Card

Logo, Full Name, Title, Phone number, Email, company name, Address,

Font styles to use
Sans Serif

Requirements
Must have
• Tag line: Elevating Capability for High Performing Teams
• Please use same colours as the logo.

```html
<!DOCTYPE html>
<html lang="en">
<head>
<meta charset="utf-8">
<title>KVOR Business Card</title>
<link href="https://fonts.googleapis.com/css2?family=Open+Sans:wght@400;600;700&family=Exo+2:wght@500&family=Arimo:wght@700&display=swap" rel="stylesheet">
<style>
  :root {
    --teal: #04a9c2;
    --ink: #111213;
    --paper: #ffffff;
    --grey: #8a8d90;
    --rule: #cfd2d4;
    --rule-dark: #3a3c3e;
    --backdrop: #e9eaeb;
    --text-light: #f2f2f2;
  }
  * { box-sizing: border-box; margin: 0; padding: 0; }
  html, body { width: 1200px; height: 900px; overflow: hidden; }
  body { background: var(--backdrop); position: relative; font-family: "Open Sans", Arial, sans-serif; }

  .card { position: absolute; overflow: hidden; box-shadow: 0 6px 18px rgba(0,0,0,.18); }
  .card--front { left: 140px; top: 100px; width: 588px; height: 363px; background: var(--paper); }
  .card--back { left: 388px; top: 497px; width: 567px; height: 351px; background: var(--ink); }

  .front-shapes { position: absolute; inset: 0; }

  .brand-name { position: absolute; font-family: "Open Sans", Arial, sans-serif; font-weight: 700; color: var(--teal); letter-spacing: 4px; line-height: 1; text-align: center; }
  .card--front .brand-name { left: 135px; width: 320px; top: 68px; font-size: 74px; }
  .card--back .brand-name { left: 82px; width: 400px; top: 88px; font-size: 80px; }

  .brand-rule { position: absolute; height: 2px; background: var(--rule); }
  .card--front .brand-rule { left: 135px; width: 320px; top: 150px; }
  .card--back .brand-rule { left: 82px; width: 400px; top: 185px; background: var(--rule-dark); }

  .holder { position: absolute; left: 45px; top: 238px; color: var(--text-light); }
  .holder__name { font-size: 18px; font-weight: 600; letter-spacing: .3px; line-height: 22px; }
  .holder__title { font-size: 15px; line-height: 20px; margin-bottom: 8px; }
  .holder__address { font-size: 15px; line-height: 18px; }

  .contacts { position: absolute; left: 306px; top: 262px; list-style: none; color: var(--text-light); font-size: 15px; line-height: 20px; }
  .contacts li { display: flex; align-items: center; gap: 6px; }
  .contacts svg { width: 10px; height: 10px; fill: var(--teal); flex: none; }

  .method-name { position: absolute; left: 0; width: 100%; top: 188px; text-align: center; font-family: "Exo 2", Arial, sans-serif; font-weight: 500; color: var(--teal); font-size: 23px; line-height: 26px; letter-spacing: 1px; }
  .method-name .joiner { color: var(--grey); }

  .tagline { position: absolute; left: 0; width: 100%; top: 270px; height: 60px; background: var(--teal); display: flex; align-items: center; justify-content: center; font-family: "Arimo", Arial, sans-serif; font-weight: 700; font-size: 16px; color: var(--ink); letter-spacing: .3px; }
</style>
</head>
<body>

<section class="card card--front" aria-label="Business card front">
  <svg class="front-shapes" viewBox="0 0 588 363" width="588" height="363" aria-hidden="true">
    <polygon points="0,190 245,190 275,225 588,225 588,363 0,363" fill="var(--ink)"/>
    <polygon points="254,198 588,198 588,225 275,225" fill="var(--teal)"/>
  </svg>
  <div class="brand-name">KVOR</div>
  <div class="brand-rule"></div>

  <div class="holder">
    <p class="holder__name">JOHN SMITH</p>
    <p class="holder__title">Managing Director</p>
    <p class="holder__address">12345, Address Goes Here<br>Country Name here, 123456</p>
  </div>

  <ul class="contacts">
    <li><svg viewBox="0 0 10 10"><path d="M2 0.5 L3.6 2.6 L2.7 3.6 Q3.8 5.9 6.2 7.3 L7.2 6.4 L9.5 8 L8.3 9.6 Q3.9 9.2 0.5 1.9 Z"/></svg>044-555 010 270</li>
    <li><svg viewBox="0 0 10 10"><path d="M0 2 H10 V8.5 H0 Z M0.6 2.4 L5 5.6 L9.4 2.4" stroke="var(--ink)" stroke-width=".8"/></svg>info@kvorlattice.com</li>
    <li><svg viewBox="0 0 10 10"><circle cx="5" cy="5" r="4.6"/><path d="M0.6 5 H9.4 M5 0.4 V9.6 M5 0.6 Q1.6 5 5 9.4 M5 0.6 Q8.4 5 5 9.4" stroke="var(--ink)" stroke-width=".7" fill="none"/></svg>www.kvorlattice.com</li>
  </ul>
</section>

<section class="card card--back" aria-label="Business card back">
  <div class="brand-name">KVOR</div>
  <div class="brand-rule"></div>
  <p class="method-name">COHERENT LATTICE<br><span class="joiner">OF</span> ADAPTIVE REASONING METHOD</p>
  <p class="tagline">ELEVATING CAPABILITY FOR HIGH PERFORMING TEAMS</p>
</section>

</body>
</html>
```